Navoro & Omvar Automotive Repair Shop. Need a new website design.

We specialize in Navoro & Omvar auto repair, but also work on other Asian import vehicles. We have been in business for 7 years and pride ourselves on high quality auto repair that is fixed right the first time. Would like the automotive repair website to incorporate the colors black, red and white if possible and have our logo and some Navoro and Omvar vehicles included in the website.

Target Market(s)

Navoro & Omvar vehicle owners

Industry/Entity Type

Automotive Repair

Coding

Coded - Design and coding required

Number of Pages Required

5+ page

Colors
EB3D1F
EC4F4E
F09395
F8D3D4
FCEDEE

Requirements
Must have
• Home, Services, Contact Us, Schedule appointment, and a gallery tab that I can add shop pictures to when completed.
Nice to have
• Would like to see example pictures of job next to each service listed.
Should not have
• Service not related to auto repair. Ex. auto detailing, towing, car wash

```html
<!DOCTYPE html>
<html lang="en">
<head>
<meta charset="utf-8">
<title>Kestrel Automotive – Contact Us</title>
<link rel="stylesheet" href="https://fonts.googleapis.com/css2?family=Fira+Sans+Condensed:ital,wght@0,500;0,600;0,700;1,400;1,500&family=Open+Sans:wght@400;600;700&family=Poppins:ital,wght@1,400;1,600&display=swap">
<style>
:root{
  --red:#ec0000;
  --red-soft:#eb3d1f;
  --black:#000;
  --ink:#111;
  --grey-bg:#f2f2f2;
  --white:#fff;
  --line:#cfcfcf;
  --muted:#8a8a8a;
  --footer:#161616;
}
*{box-sizing:border-box;margin:0;padding:0}
html,body{width:1200px;height:2229px;overflow:hidden}
body{position:relative;background:var(--white);font-family:"Open Sans",sans-serif;color:var(--ink)}
.abs{position:absolute}
.cond{font-family:"Fira Sans Condensed",sans-serif}

/* header */
.site-header{left:0;top:0;width:1200px;height:122px;background:var(--black)}
.brand{left:126px;top:20px;width:122px;height:86px;border:2px solid var(--red);border-radius:10px 10px 40px 40px;display:flex;align-items:center;justify-content:center;gap:6px;color:var(--white);font-family:"Fira Sans Condensed",sans-serif;font-weight:700;font-size:19px;letter-spacing:.5px}
.brand .dot{width:10px;height:10px;background:var(--red);border-radius:50%}
.perk{top:22px;display:flex;align-items:center;gap:8px;font-family:"Poppins",sans-serif;font-style:italic;font-size:13px;color:#ddd;line-height:16px}
.perk .ico{width:34px;height:34px;border-radius:50%;background:#e6e6e6;display:flex;align-items:center;justify-content:center}
.perk .hl{color:var(--red);font-weight:600}
.stars{color:var(--red);font-size:15px;letter-spacing:1px;font-style:normal}
.nav{top:94px;left:582px;display:flex;gap:32px;font-size:11px;font-weight:700;color:var(--white)}
.nav .active{color:var(--red)}
.header-rule{left:0;top:119px;width:360px;height:3px;background:var(--red)}

/* hero */
.hero{left:0;top:122px;width:1200px;height:315px;background:linear-gradient(100deg,#5a1016 0%,#3a2a2a 45%,#2a2a2c 60%,#4a4a4c 100%)}
.hero-tint{left:0;top:122px}
.eyebrow{display:flex;align-items:center;gap:12px;font-size:11px;font-weight:600;letter-spacing:.5px}
.eyebrow::before{content:"";width:40px;height:1px;background:currentColor}
.hero .eyebrow{position:absolute;left:113px;top:106px;color:var(--white)}
.hero h1{position:absolute;left:111px;top:124px;font-family:"Fira Sans Condensed",sans-serif;font-weight:700;font-size:50px;color:var(--white)}
.hero p{position:absolute;left:111px;top:186px;width:330px;font-size:11.5px;line-height:17px;color:#eee}

/* contact cards */
.touch{left:0;top:437px;width:1200px;height:484px;background:var(--grey-bg)}
.touch h2{position:absolute;top:104px;width:1200px;text-align:center;font-family:"Fira Sans Condensed",sans-serif;font-weight:700;font-size:37px;color:var(--black)}
.touch .sub{position:absolute;top:152px;width:1200px;text-align:center;font-family:"Fira Sans Condensed",sans-serif;font-style:italic;font-size:20px;line-height:23px}
.touch .sub a{color:var(--red)}
.card{top:240px;width:236px;height:173px;background:var(--black);color:var(--white);text-align:center}
.card.feature{background:var(--red);clip-path:polygon(43px 0,100% 0,100% 100%,0 100%,0 52px);box-shadow:0 10px 20px rgba(0,0,0,.2)}
.card .ring{width:45px;height:45px;margin:32px auto 0;border:2px solid var(--white);border-radius:50%;display:flex;align-items:center;justify-content:center}
.card h3{margin-top:14px;font-family:"Fira Sans Condensed",sans-serif;font-weight:600;font-size:15px}
.card p{margin-top:6px;font-size:11px;line-height:15px}

/* appointment form */
.appt .eyebrow{position:absolute;left:113px;top:977px;color:var(--red);font-family:"Fira Sans Condensed",sans-serif;font-size:11px}
.appt h2{position:absolute;left:113px;top:1004px;font-family:"Fira Sans Condensed",sans-serif;font-weight:700;font-size:37px;line-height:37px}
.appt .lead{position:absolute;left:113px;top:1093px;width:400px;font-size:11.5px;line-height:18px;color:#333}
.field{height:43px;border:1px solid var(--line);display:flex;align-items:center;justify-content:space-between;padding:0 14px 0 18px;font-family:"Fira Sans Condensed",sans-serif;font-style:italic;font-size:12px;color:var(--muted)}
.field.filled{border-color:#222;color:#111;font-weight:500}
.field .fi{width:21px;height:21px;border:1px solid #777;border-radius:50%;display:flex;align-items:center;justify-content:center}
.field.msg{align-items:flex-start;padding-top:14px}
.submit{left:113px;top:1391px;width:186px;height:44px;background:var(--red);color:var(--white);clip-path:polygon(22px 0,100% 0,100% 100%,0 100%,0 22px);display:flex;align-items:center;justify-content:center;gap:7px;font-family:"Fira Sans Condensed",sans-serif;font-weight:600;font-size:12px}
.promo-bg{left:606px;top:1047px}
.promo-photo{left:612px;top:960px;width:300px;height:463px;background:linear-gradient(180deg,#c9c9c9 0%,#2f5fb5 35%,#2348a0 75%,#222 100%);border-radius:120px 120px 0 0}
.promo-small{left:906px;top:1135px;font-family:"Fira Sans Condensed",sans-serif;font-weight:600;font-size:12px;line-height:15px;color:var(--white)}
.promo-big{left:906px;top:1173px;font-family:"Fira Sans Condensed",sans-serif;font-weight:700;font-size:46px;line-height:41px;color:var(--white)}

/* map */
.map{left:0;top:1497px;width:1200px;height:331px;background:linear-gradient(135deg,#ecebe6 0%,#e9e2d2 50%,#e6e8e4 100%)}

/* footer */
.site-footer{left:0;top:1828px;width:1200px;height:401px;background:var(--footer)}
.foot-brand{left:113px;top:1892px;width:187px;height:158px;border:3px solid var(--red);border-radius:14px 14px 70px 70px;display:flex;align-items:center;justify-content:center;gap:8px;color:var(--white);font-family:"Fira Sans Condensed",sans-serif;font-weight:700;font-size:28px}
.foot-brand .dot{width:14px;height:14px;background:var(--red);border-radius:50%}
.badge{height:36px;background:var(--white)}
.foot-h{font-family:"Fira Sans Condensed",sans-serif;font-weight:600;font-size:19px;color:var(--red)}
.links{left:367px;top:1929px;list-style:none;font-size:11.5px;color:#ddd;line-height:32px}
.contact-row{left:506px;display:flex;align-items:center;gap:12px;font-size:11.5px;line-height:16px;color:#ddd}
.contact-row .ci{width:30px;height:30px;border-radius:50%;background:#d9d9d9;display:flex;align-items:center;justify-content:center;flex:none}
.contact-row b{color:var(--red);font-weight:400}
.foot-map{left:793px;top:1890px;width:295px;height:209px;background:linear-gradient(135deg,#f1f1ef,#dfe6ea);clip-path:polygon(50px 0,100% 0,100% 100%,0 100%,0 50px);border-radius:4px}
.social{top:2183px;width:28px;height:28px;border-radius:50%;background:#5a5a5a;border:1px solid #888}
.copy{left:0;top:2187px}
.copy-text{right:108px;top:2203px;font-size:11.5px;color:var(--white)}
</style>
</head>
<body>

<header class="abs site-header">
  <div class="abs brand"><span class="dot"></span>KESTREL</div>
  <div class="abs perk" style="left:519px">
    <span class="ico"><svg width="18" height="18" viewBox="0 0 24 24" fill="none" stroke="#333" stroke-width="2"><circle cx="12" cy="9" r="6"/><path d="M8 14l-2 8 6-3 6 3-2-8"/></svg></span>
    <span><span class="stars">★★★★★</span><br>5 Star Service</span>
  </div>
  <div class="abs perk" style="left:715px">
    <span class="ico"><svg width="18" height="18" viewBox="0 0 24 24" fill="none" stroke="#333" stroke-width="2"><path d="M4 20L14 10M18 4l2 2-4 4-2-2zM4 4l16 16"/></svg></span>
    <span>Quality Service<br><span class="hl">Guarantee</span></span>
  </div>
  <div class="abs perk" style="left:921px">
    <span class="ico"><svg width="18" height="18" viewBox="0 0 24 24" fill="#333"><path d="M6 3l4 4-2 3c1 2 4 5 6 6l3-2 4 4-3 3C10 21 3 14 3 6z"/></svg></span>
    <span>Call Us For Booking<br><span class="hl">555.013.4821</span></span>
  </div>
  <nav class="abs nav">
    <span>HOME</span><span>ABOUT US</span><span>SERVICES ⌄</span><span>GALLERY</span><span>TESTIMONIALS</span><span class="active">CONTACT US</span>
  </nav>
  <div class="abs header-rule"></div>
  <svg class="abs" style="left:330px;top:80px" width="45" height="42"><polygon points="28,0 38,0 10,42 0,42" fill="var(--red)"/><polygon points="38,0 42,0 14,42 10,42" fill="#fff"/></svg>
</header>

<section class="abs hero" role="img" aria-label="Mechanic's gloved hand working on a car engine, red-tinted on the left">
  <svg class="abs" style="left:0;top:0" width="620" height="315"><polygon points="0,0 620,0 460,315 0,315" fill="#b0101a" opacity=".45"/></svg>
  <div class="eyebrow">CONTACT</div>
  <h1>Contact Us Today!</h1>
  <p>Quisque lorem neque, ultricies eget risus quis, fringilla interdum augue. Donec sollicitudin in ante sed consequat.</p>
</section>

<section class="abs touch">
  <svg class="abs" style="left:330px;top:0" width="870" height="37"><polygon points="0,0 870,0 870,28 745,30 430,17 45,37" fill="var(--red)"/></svg>
  <h2>Have Questions? Get In Touch!</h2>
  <p class="sub">We're open for business 5 days a week. See<br>the <a>opening hours</a> of our workshop</p>

  <div class="abs card" style="left:113px">
    <div class="ring"><svg width="20" height="20" viewBox="0 0 24 24" fill="#fff"><path d="M12 2a7 7 0 0 0-7 7c0 5 7 13 7 13s7-8 7-13a7 7 0 0 0-7-7zm0 9.5a2.5 2.5 0 1 1 0-5 2.5 2.5 0 0 1 0 5z"/></svg></div>
    <h3>Address</h3><p>412 Harbor Field Way #3<br>Brookvale, TX 75900</p>
  </div>
  <div class="abs card feature" style="left:360px">
    <div class="ring"><svg width="20" height="20" viewBox="0 0 24 24" fill="#fff"><path d="M6 3l4 4-2 3c1 2 4 5 6 6l3-2 4 4-3 3C10 21 3 14 3 6z"/></svg></div>
    <h3>Phone</h3><p>Office: 555.013.4821<br>Cell: 555.019.2736</p>
  </div>
  <div class="abs card" style="left:606px">
    <div class="ring"><svg width="18" height="18" viewBox="0 0 24 24" fill="#fff"><path d="M3 6h18v12H3z"/><path d="M3 6l9 7 9-7" stroke="#000" stroke-width="1.6" fill="none"/></svg></div>
    <h3>Email</h3><p>hello@kestrelauto.example</p>
  </div>
  <div class="abs card" style="left:853px">
    <div class="ring"><svg width="20" height="20" viewBox="0 0 24 24"><circle cx="12" cy="12" r="10" fill="#fff"/><path d="M12 6v6l3 2" stroke="#000" stroke-width="2" fill="none"/></svg></div>
    <h3>Opening Hours</h3><p>Monday to Friday<br>8:30-6pm</p>
  </div>
</section>

<section class="appt">
  <div class="eyebrow">GET AN APPOINTMENT</div>
  <h2>Still have query, then<br>fill out the form!</h2>
  <p class="lead">Maecenas tempus, tellus eget condimentum rhoncus, sem quam semper libero, sit amet adipiscing sem neque sed ipsum. Nam quam nunclt.</p>

  <div class="abs field filled" style="left:113px;top:1162px;width:237px">Dana Fields |<span class="fi"><svg width="11" height="11" viewBox="0 0 24 24" fill="#333"><circle cx="12" cy="8" r="5"/><path d="M3 22c0-6 18-6 18 0z"/></svg></span></div>
  <div class="abs field" style="left:358px;top:1162px;width:237px">+ 00 123 456 7890<span class="fi"><svg width="11" height="11" viewBox="0 0 24 24" fill="#777"><path d="M6 3l4 4-2 3c1 2 4 5 6 6l3-2 4 4-3 3C10 21 3 14 3 6z"/></svg></span></div>
  <div class="abs field" style="left:113px;top:1212px;width:237px">dana@example.com<span class="fi"><svg width="10" height="10" viewBox="0 0 24 24" fill="#777"><path d="M2 5h20v14H2z"/></svg></span></div>
  <div class="abs field" style="left:358px;top:1212px;width:237px">Service<span class="fi"><svg width="10" height="10" viewBox="0 0 24 24" fill="none" stroke="#777" stroke-width="2"><path d="M6 9l6 6 6-6"/></svg></span></div>
  <div class="abs field msg" style="left:113px;top:1264px;width:482px;height:103px">Message<span class="fi"><svg width="10" height="10" viewBox="0 0 24 24" fill="#777"><path d="M3 21l3-8 11-11 5 5-11 11z"/></svg></span></div>
  <div class="abs submit"><svg width="14" height="14" viewBox="0 0 24 24" fill="#fff"><path d="M22 2L2 10l7 3 3 7z"/></svg>SUBMIT</div>

  <svg class="abs promo-bg" width="594" height="376"><polygon points="184,0 594,0 594,376 0,376" fill="var(--red)"/></svg>
  <div class="abs promo-photo" role="img" aria-label="Smiling mechanic in blue overalls holding a tyre"></div>
  <div class="abs promo-small">Our team will get in touch<br>with you shortly</div>
  <div class="abs promo-big">Ask us<br>anything,<br>we’d love<br>to answer!</div>
</section>

<div class="abs map" role="img" aria-label="Street map showing the shop location"></div>

<footer class="abs site-footer"></footer>
<div class="abs foot-brand"><span class="dot"></span>KESTREL</div>
<div class="abs badge" style="left:113px;top:2062px;width:92px"></div>
<div class="abs badge" style="left:210px;top:2062px;width:75px"></div>
<div class="abs badge" style="left:113px;top:2103px;width:50px"></div>
<div class="abs badge" style="left:166px;top:2103px;width:92px"></div>

<div class="abs foot-h" style="left:367px;top:1887px">Quick Links.</div>
<ul class="abs links"><li>Home</li><li>About Us</li><li>Services</li><li>Gallery</li><li>Testimonials</li><li>Contact Us</li></ul>

<div class="abs foot-h" style="left:516px;top:1887px">Contact Us</div>
<div class="abs contact-row" style="top:1935px"><span class="ci"><svg width="14" height="14" viewBox="0 0 24 24" fill="#444"><path d="M12 2a7 7 0 0 0-7 7c0 5 7 13 7 13s7-8 7-13a7 7 0 0 0-7-7z"/></svg></span><span>412 Harbor Field Way #3<br>Brookvale, TX 75900</span></div>
<div class="abs contact-row" style="top:1982px"><span class="ci"><svg width="14" height="14" viewBox="0 0 24 24" fill="#444"><path d="M6 3l4 4-2 3c1 2 4 5 6 6l3-2 4 4-3 3C10 21 3 14 3 6z"/></svg></span><span><b>OFFICE:</b> 555.013.4821<br><b>Phone:</b> 555.019.2736</span></div>
<div class="abs contact-row" style="top:2032px"><span class="ci"><svg width="13" height="13" viewBox="0 0 24 24" fill="#444"><path d="M2 5h20v14H2z"/></svg></span><span>hello@kestrelauto.example</span></div>
<div class="abs contact-row" style="top:2079px"><span class="ci"><svg width="14" height="14" viewBox="0 0 24 24"><circle cx="12" cy="12" r="10" fill="#444"/><path d="M12 6v6l3 2" stroke="#ddd" stroke-width="2" fill="none"/></svg></span><span><b>Hours of Operation:</b> M-F 8:30-6pm</span></div>

<div class="abs foot-map" role="img" aria-label="Small area map of the shop's neighbourhood"></div>

<div class="abs social" style="left:151px"></div>
<div class="abs social" style="left:185px"></div>
<div class="abs social" style="left:219px"></div>

<svg class="abs copy" width="1200" height="42"><polygon points="330,0 1200,0 1200,42 305,42" fill="var(--red)"/><polygon points="0,40 312,40 310,42 0,42" fill="var(--red)"/><polygon points="322,0 330,0 305,42 297,42" fill="#fff"/></svg>
<div class="abs copy-text">Copyright © 2024 Kestrel Automotive LLC. All Rights Reserved.</div>

</body>
</html>
```